VOMRA Pty Ltd Business Card

Looking for a simple yet eye-catching double-sided business card design using my company logo on one side and contact details on the other.

Target Market(s)

Government

Industry/Entity Type

Communication Systems Engineering

Contact Information for Business Card

VOMRA Pty Ltd

Requirements
Nice to have
• Would be great to have a QR code so details can be scanned into contacts

```html
<!DOCTYPE html>
<html lang="en">
<head>
<meta charset="utf-8">
<title>VOMRA Pty Ltd Business Card</title>
<link href="https://fonts.googleapis.com/css2?family=Open+Sans:wght@400;700;800&display=swap" rel="stylesheet">
<style>
  :root {
    --page: #e9e9e7;
    --slate: #37414a;
    --ink: #1e1e1e;
    --white: #ffffff;
    --emboss: #252d33;
    --mark-faint: #2b3238;
  }
  * { box-sizing: border-box; margin: 0; padding: 0; }
  html, body { width: 1200px; height: 780px; overflow: hidden; }
  body {
    background: var(--page);
    font-family: "Open Sans", Arial, sans-serif;
    display: flex;
    align-items: center;
    justify-content: center;
    gap: 40px;
  }
  .card {
    position: relative;
    width: 540px;
    height: 310px;
    overflow: hidden;
    box-shadow: 0 10px 28px rgba(0,0,0,0.22);
  }

  /* Contact side */
  .card--contact { background: var(--slate); }
  .contact__band {
    position: absolute;
    left: 0; top: 0;
    width: 100%;
    height: 170px;
    background: var(--ink);
  }
  .contact__band-tail {
    position: absolute;
    left: 0; top: 170px;
    width: 100px;
    height: 0;
  }
  .brand {
    position: absolute;
    left: 28px; top: 34px;
    display: flex;
    align-items: center;
    gap: 14px;
    color: var(--white);
    font-weight: 800;
    font-size: 50px;
    letter-spacing: 3px;
    line-height: 1;
  }
  .brand__square {
    width: 40px; height: 40px;
    border: 3px solid var(--white);
  }
  .holder {
    position: absolute;
    right: 40px; top: 108px;
    text-align: right;
    color: var(--white);
  }
  .holder__name { font-weight: 700; font-size: 26px; line-height: 1.1; }
  .holder__role { font-weight: 400; font-size: 15px; margin-top: 2px; }
  .holder__bar {
    position: absolute;
    right: 12px; top: 106px;
    width: 18px; height: 58px;
    background: var(--white);
  }
  .details {
    position: absolute;
    left: 24px; top: 184px;
    color: var(--white);
    font-size: 13px;
    line-height: 1.45;
    list-style: none;
  }
  .details__address { margin-bottom: 4px; }
  .details__row { display: flex; align-items: center; gap: 7px; }
  .details__row svg { width: 11px; height: 11px; fill: var(--white); flex: none; }
  .contact__mark {
    position: absolute;
    right: 70px; bottom: -30px;
    width: 150px; height: 150px;
    background: var(--mark-faint);
    opacity: 0.6;
  }

  /* Brand side */
  .card--brand { background: var(--slate); }
  .brand--emboss {
    left: 50%; top: 50%;
    transform: translate(-50%, -50%);
    color: var(--emboss);
    font-size: 70px;
    gap: 20px;
  }
  .brand--emboss .brand__square {
    width: 56px; height: 56px;
    border: 4px solid var(--emboss);
  }
</style>
</head>
<body>

  <section class="card card--contact" aria-label="Business card, contact side">
    <div class="contact__band"></div>
    <div class="contact__mark" aria-hidden="true"></div>

    <div class="brand">
      <span class="brand__square" aria-hidden="true"></span>
      <span class="brand__name">VOMRA</span>
    </div>

    <div class="holder">
      <p class="holder__name">Jordan Whitley</p>
      <p class="holder__role">Co-Founder</p>
    </div>
    <div class="holder__bar" aria-hidden="true"></div>

    <ul class="details">
      <li class="details__address">42-44 Harbour Lane Millbrook<br>NSW 2099 Australia</li>
      <li class="details__row">
        <svg viewBox="0 0 24 24" aria-hidden="true"><path d="M6.6 10.8a15.1 15.1 0 0 0 6.6 6.6l2.2-2.2c.3-.3.7-.4 1-.2 1.1.4 2.3.6 3.6.6.6 0 1 .4 1 1V20c0 .6-.4 1-1 1A17 17 0 0 1 3 4c0-.6.4-1 1-1h3.5c.6 0 1 .4 1 1 0 1.3.2 2.5.6 3.6.1.3 0 .7-.2 1z"/></svg>
        <span>(555) 014-2231</span>
      </li>
      <li class="details__row">
        <svg viewBox="0 0 24 24" aria-hidden="true"><path d="M2 5h20v14H2zM4 7v.5l8 5 8-5V7l-8 5z"/></svg>
        <span>www.vomra.com.au</span>
      </li>
      <li class="details__row">
        <svg viewBox="0 0 24 24" aria-hidden="true"><circle cx="12" cy="12" r="10"/></svg>
        <span>admin@vomra.com.au</span>
      </li>
    </ul>
  </section>

  <section class="card card--brand" aria-label="Business card, brand side">
    <div class="brand brand--emboss">
      <span class="brand__square" aria-hidden="true"></span>
      <span class="brand__name">VOMRA</span>
    </div>
  </section>

</body>
</html>
```